Animal Eye Clinic needs a Business card

We are a new veterinary ophthalmology practice (Ridgeline Pet Vision Care) and we need a business card designed. We only see animal eyes - we are not a regular veterinary clinic. We already have a logo. We are looking for a professional, good looking business card to hand out to our clients. We are looking for something simple but professional and contemporary. Our logo is likely the only picture/graphic that needs to be on the card.
Updates

Contact Information for Business Card

Delia Vossman, BSc, DVM, MSc, DipACVO
Veterinary Ophthalmologist

Phone: 250.418.3927
Email: ridgelinepetvisioncare@mailbox-example.net
Website: ridgelinepetvisioncare-example.net
Address: 1874 Thornbury Rd
Kelowna, BC, V1X 4M9

Colors

Designer to choose colors to be used in the design.

Requirements
Must have
• Our logo (attached)

```html
<!DOCTYPE html>
<html lang="en">
<head>
<meta charset="utf-8">
<title>Ridgeline Pet Vision Care – Business Card</title>
<link href="https://fonts.googleapis.com/css2?family=Roboto:ital,wght@0,400;0,500;0,700;1,700&display=swap" rel="stylesheet">
<style>
  :root {
    --teal: #1c98a8;
    --teal-dark: #15808e;
    --ink-grey: #6b6b6b;
    --paper: #ffffff;
    --mist: #dcecef;
    --mist-soft: #eef5f6;
    --backdrop: #d9dadc;
  }
  * { box-sizing: border-box; margin: 0; padding: 0; }
  html, body {
    width: 1200px; height: 800px; overflow: hidden;
    background: var(--backdrop);
    font-family: "Roboto", Arial, sans-serif;
  }
  .canvas {
    width: 1200px; height: 800px;
    display: flex; flex-direction: column;
    align-items: center; justify-content: center; gap: 40px;
  }
  .card {
    width: 600px; height: 343px; position: relative; overflow: hidden;
    box-shadow: 0 6px 18px rgba(0,0,0,.18);
  }

  /* Front */
  .card--front { background: var(--teal); color: var(--paper); }
  .card--front .brand {
    position: absolute; left: 0; right: 0; top: 118px;
    display: flex; align-items: center; justify-content: center; gap: 14px;
  }
  .brand__dot { width: 22px; height: 22px; border-radius: 50%; background: currentColor; flex: none; }
  .brand__name {
    font-weight: 700; font-size: 30px; letter-spacing: .5px; text-transform: uppercase; line-height: 1;
  }
  .card--front .front-url {
    position: absolute; left: 0; right: 0; top: 262px; text-align: center;
    font-size: 15px; letter-spacing: .6px;
  }

  /* Back */
  .card--back { background: var(--paper); }
  .back-art {
    position: absolute; left: 0; top: 0; width: 600px; height: 343px;
  }
  .person { position: absolute; left: 32px; top: 30px; }
  .person__name { color: var(--teal); font-weight: 700; font-size: 22px; text-transform: uppercase; letter-spacing: .3px; }
  .person__creds { color: var(--teal); font-weight: 700; font-size: 14px; margin-top: 2px; }
  .person__role { color: var(--ink-grey); font-size: 15px; margin-top: 4px; }
  .card--back .brand {
    position: absolute; right: 34px; top: 128px;
    display: flex; align-items: center; gap: 10px; color: var(--teal);
  }
  .card--back .brand__name { font-size: 21px; }
  .card--back .brand__dot { width: 16px; height: 16px; }
  .contact {
    position: absolute; right: 34px; bottom: 26px; text-align: right;
    color: var(--ink-grey); font-size: 14.5px; line-height: 1.35;
  }
  .contact__address { margin-bottom: 8px; }
  .contact__line { display: flex; justify-content: flex-end; align-items: center; gap: 8px; }
  .contact__icon { width: 14px; height: 14px; flex: none; color: var(--teal); }
</style>
</head>
<body>
<main class="canvas">
  <section class="card card--front">
    <div class="brand">
      <span class="brand__dot"></span>
      <span class="brand__name">Ridgeline Pet Vision Care</span>
    </div>
    <p class="front-url">ridgelinepetvisioncare-example.net</p>
  </section>

  <section class="card card--back">
    <svg class="back-art" viewBox="0 0 600 343" role="img" aria-label="Faint pale-teal silhouettes of a dog, cat and horse">
      <defs>
        <linearGradient id="mistFade" x1="0" y1="1" x2="1" y2="0">
          <stop offset="0" stop-color="#dcecef"/>
          <stop offset="1" stop-color="#eef5f6" stop-opacity="0"/>
        </linearGradient>
      </defs>
      <path d="M0 343 L0 170 Q140 120 260 60 L300 40 L320 200 Q300 300 260 343 Z" fill="url(#mistFade)"/>
    </svg>

    <div class="person">
      <h1 class="person__name">Delia Vossman</h1>
      <p class="person__creds">BSc, DVM, MSc, DipACVO</p>
      <p class="person__role">Veterinary Ophthalmologist</p>
    </div>

    <div class="brand">
      <span class="brand__dot"></span>
      <span class="brand__name">Ridgeline Pet Vision Care</span>
    </div>

    <address class="contact" style="font-style:normal">
      <p class="contact__address">1874 Thornbury Rd<br>Kelowna, BC, V1X 4M9</p>
      <p class="contact__line">250.418.3927
        <svg class="contact__icon" viewBox="0 0 16 16"><path fill="currentColor" d="M3.6 1.5l2.2 2.6-1.3 1.7c.9 2 2.5 3.7 4.6 4.7l1.6-1.4 2.7 2.1-1.2 2.6C6.6 13.6 2.3 9.3 1.1 3z"/></svg>
      </p>
      <p class="contact__line">ridgelinepetvisioncare@mailbox-example.net
        <svg class="contact__icon" viewBox="0 0 16 16"><rect x="1.5" y="3.5" width="13" height="9" fill="none" stroke="currentColor" stroke-width="1.5"/><path d="M1.5 3.5L8 9l6.5-5.5" fill="none" stroke="currentColor" stroke-width="1.5"/></svg>
      </p>
      <p class="contact__line">ridgelinepetvisioncare-example.net
        <svg class="contact__icon" viewBox="0 0 16 16"><g fill="none" stroke="currentColor" stroke-width="1.3"><circle cx="8" cy="8" r="6.5"/><ellipse cx="8" cy="8" rx="3" ry="6.5"/><path d="M1.5 8h13M2.5 4.8h11M2.5 11.2h11"/></g></svg>
      </p>
    </address>
  </section>
</main>
</body>
</html>
```